Fernhale Business Card Design

We are looking for a fresh business card design for our new logo. We would like a business card that is unique but friendly. We are in the window coverings business offering blinds, shutters and shades for homes.

Target Market(s)

Targeting the end-consumer

Industry/Entity Type

Business

Requirements
Must have
• Must have a dedicates space for a photo of our sales person. Must contain our new logo (attached).

```html
<!DOCTYPE html>
<html lang="en">
<head>
<meta charset="utf-8">
<title>Fernhale Business Card</title>
<link rel="stylesheet" href="https://fonts.googleapis.com/css2?family=Open+Sans:wght@400;600&display=swap">
<style>
  :root {
    --leaf-green: #8bc540;
    --pale-green: #e8f3d9;
    --card-white: #ffffff;
    --ink-grey: #5f6062;
    --backdrop: #e9e7e4;
    --shadow: rgba(0, 0, 0, 0.18);
  }
  * { margin: 0; padding: 0; box-sizing: border-box; }
  html, body {
    width: 1200px;
    height: 900px;
    overflow: hidden;
    background: var(--backdrop);
    font-family: "Open Sans", Arial, sans-serif;
  }
  .canvas {
    position: relative;
    width: 1200px;
    height: 900px;
  }
  .card {
    position: absolute;
    overflow: hidden;
    box-shadow: 0 6px 18px var(--shadow);
  }
  .card-front {
    left: 155px;
    top: 57px;
    width: 588px;
    height: 363px;
    background: var(--leaf-green);
    color: var(--card-white);
  }
  .person-name {
    position: absolute;
    left: 32px;
    top: 47px;
    font-size: 22px;
    font-weight: 600;
    line-height: 1.1;
  }
  .person-role {
    position: absolute;
    left: 32px;
    top: 73px;
    font-size: 15px;
    font-weight: 400;
  }
  .contact-list {
    position: absolute;
    left: 32px;
    top: 229px;
    list-style: none;
    font-size: 15px;
    line-height: 21px;
  }
  .contact-list li {
    display: flex;
    align-items: center;
    gap: 7px;
  }
  .contact-icon {
    width: 12px;
    height: 12px;
    fill: var(--card-white);
    flex: none;
  }
  .photo-slot {
    position: absolute;
    left: 325px;
    top: 0;
    width: 263px;
    height: 363px;
    background: linear-gradient(160deg, var(--card-white) 0%, var(--pale-green) 100%);
    border-top-left-radius: 70px;
    border-bottom-left-radius: 70px;
  }
  .card-back {
    left: 390px;
    top: 462px;
    width: 566px;
    height: 350px;
    background: var(--card-white);
  }
  .brand {
    position: absolute;
    left: 106px;
    top: 136px;
    display: flex;
    align-items: center;
    gap: 18px;
  }
  .brand-square {
    width: 78px;
    height: 78px;
    background: var(--leaf-green);
  }
  .brand-name {
    font-size: 52px;
    font-weight: 400;
    color: var(--ink-grey);
    line-height: 1;
  }
  .back-web {
    position: absolute;
    left: 0;
    right: 0;
    top: 276px;
    text-align: center;
    font-size: 18px;
    color: var(--ink-grey);
  }
  .back-web .accent { color: var(--leaf-green); }
</style>
</head>
<body>
<main class="canvas">
  <section class="card card-front">
    <h1 class="person-name">Daniel Hartley</h1>
    <p class="person-role">Managing Director</p>
    <ul class="contact-list">
      <li>
        <svg class="contact-icon" viewBox="0 0 12 12" aria-hidden="true"><path d="M3 0h6a1 1 0 0 1 1 1v10a1 1 0 0 1-1 1H3a1 1 0 0 1-1-1V1a1 1 0 0 1 1-1zm0 1.5v8h6v-8z"/></svg>
        044-987 654 321
      </li>
      <li>
        <svg class="contact-icon" viewBox="0 0 12 12" aria-hidden="true"><path d="M0 4c1-2 3-3 6-3s5 1 6 3l-2 1-1-1.5H3L2 5z"/><rect x="2" y="6" width="8" height="5" rx="1"/></svg>
        044-987 654 321
      </li>
      <li>
        <svg class="contact-icon" viewBox="0 0 12 12" aria-hidden="true"><path d="M0 2h12v8H0zm1 1v.3l5 3.3 5-3.3V3z"/></svg>
        hello@fernhale.com
      </li>
      <li>
        <svg class="contact-icon" viewBox="0 0 12 12" aria-hidden="true"><circle cx="6" cy="6" r="6"/><path d="M3 4c1 0 2 1 1.5 2S5 8 4 9M8 3c-.5 1 .5 1.5 1.5 2M7 8c1 0 2 .5 2 1.5" stroke="#8bc540" stroke-width="1" fill="none"/></svg>
        www.fernhaleblinds.com
      </li>
    </ul>
    <div class="photo-slot" role="img" aria-label="Photo of the sales person"></div>
  </section>

  <section class="card card-back">
    <div class="brand">
      <span class="brand-square" aria-hidden="true"></span>
      <span class="brand-name">Fernhale</span>
    </div>
    <p class="back-web">www.<span class="accent">fernhale</span>.com</p>
  </section>
</main>
</body>
</html>
```